DESKHAVEN COSPACE Website design and coding

DESKHAVEN COSPACE

DESKHAVEN is Cedar Shoals’ friendly (and fully local) shared business co-working space. We share the same upscale, casual work environment, but we work independently on our own (or our team’s) projects and goals. For only a flat $195 membership fee per month, you have your very own all-inclusive, fun, personal business office environment. Website is written (Word file #12, below); and all pictures etc provided. Galveston is a beachy, coastal, historic city an hour from Houston, Texas USA. Logo (file 11 below) is temporary only.

Target Market(s)

Outside sales people, medical students looking for study hall, Houston companies looking for local office, real estate agents, graphic artists, entrepreneurs, etc

Contact Information for Business Card

will discuss --want to combine with current business card with multiple businesses

Logo Text

DESKHAVEN COSPACE

Coding

Coded - Design and coding required

Number of Pages Required

5+ page

Colors
ec1f27
fbed22

Requirements
Nice to have
• maroon/wine dominant with yellow and red accents, gray base are the colors of the space--website could coordinate--but open to creative ideas/combinations

```html
<!DOCTYPE html>
<html lang="en">
<head>
<meta charset="utf-8">
<title>Deskhaven Cospace</title>
<link href="https://fonts.googleapis.com/css2?family=Montserrat:wght@400;500;600;700;800&display=swap" rel="stylesheet">
<style>
:root{
  --red:#cf0d19;
  --yellow:#fbed22;
  --ink:#111111;
  --gray:#6e6e6e;
  --white:#ffffff;
}
*{margin:0;padding:0;box-sizing:border-box}
html,body{width:1182px;height:1200px;overflow:hidden;background:var(--white)}
body{position:relative;font-family:"Montserrat",sans-serif;color:var(--ink)}
a{text-decoration:none}
.abs{position:absolute}
.brand{display:flex;align-items:center;gap:6px;font-weight:800;font-size:25px;letter-spacing:-0.5px;color:var(--gray);white-space:nowrap}
.brand .dot{width:9px;height:9px;border-radius:50%;background:var(--red)}
.site-header .brand{left:133px;top:19px}
.nav{font-size:12px;font-weight:600;text-transform:uppercase}
.nav a{color:inherit;position:absolute;white-space:nowrap}
.site-header .nav{left:0;top:27px;color:var(--ink)}
.site-header .nav a.active{color:var(--red)}
.hero-photo{left:618px;top:76px;width:564px;height:591px;background:linear-gradient(160deg,#8a8175 0%,#5c5149 35%,#c89b4a 60%,#3b3633 100%)}
.line{background:var(--yellow)}
.title-block{left:88px;top:305px;width:462px;height:74px;background:var(--yellow)}
.title{left:157px;top:246px;font-weight:800;font-size:54px;line-height:62px;letter-spacing:-0.5px;color:var(--ink);white-space:nowrap}
.intro{left:133px;top:396px;width:412px;font-size:12.6px;line-height:20.8px;font-weight:500}
.intro .price{font-size:16px;font-weight:700}
.btn{display:flex;align-items:center;gap:14px;padding-left:10px;height:42px;font-size:11px;font-weight:700;text-transform:uppercase;color:var(--white);white-space:nowrap}
.btn svg{width:24px;height:10px;flex:none}
.btn-detail{left:133px;top:541px;width:135px;background:var(--yellow)}
.btn-try{left:282px;top:541px;width:135px;background:var(--red)}
.gallery-item{top:747px;width:290px;height:181px}
.g1{left:137px;background:linear-gradient(135deg,#6b6552,#b4a88e 50%,#3e3a36)}
.g2{left:447px;background:linear-gradient(180deg,#6d5b44,#c9a253 60%,#2e2b2a)}
.g3{left:758px;background:linear-gradient(90deg,#8b8c8e,#d8d6d0 50%,#6a6c70)}
.btn-more{left:890px;top:946px;width:158px;background:var(--red);gap:8px;padding-left:9px}
.site-footer{left:0;top:1060px;width:1182px;height:113px;background:var(--red);color:var(--white)}
.site-footer .brand{left:133px;top:16px;color:var(--white)}
.site-footer .brand .dot{background:var(--white)}
.address{left:134px;top:58px;font-size:12.8px;line-height:15px;font-weight:500;font-style:normal}
.site-footer .nav{left:0;top:36px;color:var(--white)}
.copyright{left:0;top:1173px;width:1182px;height:27px;background:var(--yellow);font-size:11px;font-weight:700;padding:8px 0 0 134px}
</style>
</head>
<body>
<header class="site-header">
  <div class="brand abs"><span>DESKHAVEN</span><span class="dot"></span></div>
  <nav class="nav abs">
    <a class="active" style="left:417px">About</a>
    <a style="left:481px">Amenities</a>
    <a style="left:574px">Membership</a>
    <a style="left:690px">Pictures</a>
    <a style="left:772px">The Deskhaven Pilosophy</a>
    <a style="left:982px">Contact</a>
  </nav>
</header>

<div class="hero-photo abs" role="img" aria-label="Photo of the lounge area with a wooden table, sofa and lockers"></div>

<div class="line abs" style="left:0;top:180px;width:258px;height:5px"></div>
<div class="line abs" style="left:253px;top:180px;width:5px;height:200px"></div>
<div class="line abs" style="left:253px;top:599px;width:5px;height:149px"></div>
<div class="line abs" style="left:0;top:771px;width:137px;height:5px"></div>

<div class="title-block abs"></div>
<h1 class="title abs">DESKHAVEN<br>COSPACE</h1>

<p class="intro abs">DESKHAVEN is Cedar Shoals’ friendly (and fully local) shared business co-working space.&nbsp; We share the same upscale, casual work environment, but we work independently on our own (or our team’s) projects and goals.&nbsp; For only a flat <span class="price">$195</span> membership fee per month, you have your very own all-inclusive, fun, personal business office environment.</p>

<a class="btn btn-detail abs">View Detail
  <svg viewBox="0 0 24 10"><path d="M0 5H22M18 1l4 4-4 4" fill="none" stroke="#fff" stroke-width="1.5"/></svg></a>
<a class="btn btn-try abs">Try It Now
  <svg viewBox="0 0 24 10"><path d="M0 5H22M18 1l4 4-4 4" fill="none" stroke="#fff" stroke-width="1.5"/></svg></a>

<div class="gallery-item g1 abs" role="img" aria-label="Photo of the glass-walled entrance and kitchen"></div>
<div class="gallery-item g2 abs" role="img" aria-label="Photo of shared work tables under pendant lamps"></div>
<div class="gallery-item g3 abs" role="img" aria-label="Photo of private cubicles and printer corner"></div>

<a class="btn btn-more abs">View More Galery
  <svg viewBox="0 0 24 10"><path d="M0 5H22M18 1l4 4-4 4" fill="none" stroke="#fff" stroke-width="1.5"/></svg></a>

<footer class="site-footer abs">
  <div class="brand abs"><span>DESKHAVEN</span><span class="dot"></span></div>
  <address class="address abs">Deskhaven Cospace<br>418 Harbor Ave, Suite 204<br>Cedar Shoals, NC 28410</address>
  <nav class="nav abs">
    <a style="left:418px">About</a>
    <a style="left:482px">Amenities</a>
    <a style="left:575px">Membership</a>
    <a style="left:691px">Pictures</a>
    <a style="left:773px">The Deskhaven Pilosophy</a>
    <a style="left:983px">Contact</a>
  </nav>
</footer>
<div class="copyright abs">Copyright 2020 DESKHAVEN COSPACE</div>
</body>
</html>
```